Corvane Freight Company Business Card Design

We are a company that delivers natural saltwater (from the ocean) to aquarium companies, restaurants and home marine tanks. I would like a new business card to suit.

Must include Name, company name, abn, contact number and website as well as logo (see attached).

Looking for a design that stands out, has a clean but unique appearance.

Double and single sided entries welcome

Business

• Logo

```html
<!DOCTYPE html>
<html lang="en">
<head>
<meta charset="utf-8">
<title>Corvane Freight Company – Business Card</title>
<link rel="stylesheet" href="https://fonts.googleapis.com/css2?family=Source+Sans+3:wght@400;600;700&display=swap">
<style>
  :root {
    --stage: #141414;
    --deep-blue: #2a78e4;
    --deep-blue-dark: #1f63d2;
    --sky-blue: #3eb1f6;
    --sky-blue-light: #47b8f8;
    --white: #ffffff;
    --soft-white: rgba(255, 255, 255, 0.85);
  }
  html, body {
    margin: 0;
    padding: 0;
    width: 1200px;
    height: 427px;
    overflow: hidden;
    background: var(--stage);
    font-family: "Source Sans 3", Arial, sans-serif;
  }
  .stage {
    position: relative;
    width: 1200px;
    height: 427px;
  }
  .card {
    position: absolute;
    top: 52px;
    width: 527px;
    height: 300px;
    border-radius: 24px;
    overflow: hidden;
    color: var(--white);
  }
  .card--front {
    left: 40px;
    background: linear-gradient(180deg, var(--deep-blue) 0%, var(--deep-blue-dark) 100%);
  }
  .card--back {
    left: 605px;
    background: var(--sky-blue);
  }
  .card__wave {
    position: absolute;
    left: 0;
    top: 0;
    width: 527px;
    height: 300px;
  }
  .brand {
    position: absolute;
    left: 0;
    width: 100%;
    text-align: center;
    font-weight: 700;
    color: var(--white);
    line-height: 1;
    white-space: nowrap;
  }
  .card--front .brand {
    top: 62px;
    font-size: 32px;
  }
  .card--back .brand {
    top: 124px;
    font-size: 40px;
  }
  .brand__dot {
    display: inline-block;
    width: 0.42em;
    height: 0.42em;
    border-radius: 50%;
    background: var(--white);
    margin-right: 0.3em;
    vertical-align: 0.12em;
  }
  .holder {
    position: absolute;
    top: 148px;
    left: 0;
    width: 100%;
    text-align: center;
    font-size: 19px;
    font-weight: 700;
  }
  .holder__title {
    font-weight: 400;
    font-size: 16px;
  }
  .address {
    position: absolute;
    top: 214px;
    right: 274px;
    text-align: right;
    font-size: 13.5px;
    line-height: 19.5px;
  }
  .divider {
    position: absolute;
    left: 267px;
    top: 212px;
    width: 1px;
    height: 60px;
    background: var(--soft-white);
  }
  .contact {
    position: absolute;
    top: 212px;
    left: 280px;
    font-size: 13.5px;
    line-height: 19.5px;
  }
  .contact__row {
    display: flex;
    align-items: center;
    gap: 4px;
  }
  .contact__icon {
    width: 10px;
    height: 10px;
    flex: none;
  }
  .web {
    position: absolute;
    top: 246px;
    left: 0;
    width: 100%;
    text-align: center;
    font-size: 17px;
    letter-spacing: 3.4px;
  }
</style>
</head>
<body>
<main class="stage">

  <section class="card card--front" aria-label="Business card front">
    <svg class="card__wave" viewBox="0 0 527 300" aria-hidden="true">
      <path d="M0 236 Q263 160 527 236 L527 300 L0 300 Z" fill="#3eb1f6"/>
      <path d="M0 234 Q263 158 527 234" fill="none" stroke="#ffffff" stroke-opacity="0.55" stroke-width="2"/>
      <path d="M60 200 Q263 170 466 200" fill="none" stroke="#ffffff" stroke-opacity="0.7" stroke-width="2"/>
    </svg>

    <div class="brand"><span class="brand__dot"></span>Corvane Freight Company</div>

    <p class="holder" style="margin:0">Your name, <span class="holder__title">Title</span></p>

    <address class="address" style="font-style:normal">
      Corvane Freight LLC<br>
      Street Name, City Name<br>
      State, City Zip Code
    </address>

    <div class="divider"></div>

    <div class="contact">
      <div class="contact__row">
        <svg class="contact__icon" viewBox="0 0 10 10" aria-hidden="true">
          <circle cx="5" cy="5" r="4.3" fill="none" stroke="#fff" stroke-width="1"/>
          <path d="M3.3 2.8 L4.2 2.6 L4.6 3.8 L4 4.3 Q4.6 5.6 5.8 6.1 L6.3 5.5 L7.4 6 L7.2 6.9 Q4 7 3.3 2.8 Z" fill="#fff"/>
        </svg>
        <span>123-456-7890</span>
      </div>
      <div class="contact__row">
        <svg class="contact__icon" viewBox="0 0 10 10" aria-hidden="true">
          <circle cx="5" cy="5" r="4.3" fill="#fff"/>
          <path d="M0.8 5 H9.2 M5 0.8 Q2.6 5 5 9.2 M5 0.8 Q7.4 5 5 9.2" fill="none" stroke="#3eb1f6" stroke-width="0.7"/>
        </svg>
        <span>www.website.com</span>
      </div>
      <div class="contact__row">ABN : 0123456789</div>
    </div>
  </section>

  <section class="card card--back" aria-label="Business card back">
    <div class="brand"><span class="brand__dot"></span>Corvane Freight Company</div>
    <div class="web">www.website.com</div>
  </section>

</main>
</body>
</html>
```